New Web Design Project

Number of Pages Required

1 page

Requirements
Must have
• An Overview / Background of the Business & Services(not for profit rescue animal farm)
• The Target Market / Audience you are trying to reach (animal lovers)
• Design Specifics; any preferences or ideas for Style, Colour, Imagery, etc (no preferences)

```html
<!DOCTYPE html>
<html lang="en">
<head>
<meta charset="utf-8">
<title>Animal Farm – Subscription &amp; Events</title>
<link href="https://fonts.googleapis.com/css2?family=Roboto:wght@300;400&family=Courgette&family=Open+Sans:wght@400;700&display=swap" rel="stylesheet">
<style>
  :root {
    --plum: #675d68;
    --frame-line: #a59ca6;
    --page-bg: #f2f2f2;
    --card-bg: #ffffff;
    --input-bg: #e3e3e3;
    --button-blue: #1e7fe0;
    --ink: #000000;
    --body-text: #555555;
    --white: #ffffff;
    --rule-grey: #cccccc;
  }
  * { box-sizing: border-box; margin: 0; padding: 0; }
  html, body { width: 1200px; height: 1000px; overflow: hidden; }
  body { position: relative; background: var(--page-bg); font-family: "Open Sans", sans-serif; }

  .subscription { position: absolute; left: 0; top: 0; width: 1200px; height: 335px; background: var(--plum); }
  .subscription__frame { position: absolute; left: 17px; top: 1px; width: 1166px; height: 311px; border: 1px solid var(--frame-line); }
  .subscription__title { position: absolute; left: 0; width: 100%; top: 56px; text-align: center; font-family: "Roboto", sans-serif; font-weight: 300; font-size: 50px; line-height: 60px; color: var(--white); }

  .divider { position: absolute; left: 510px; width: 173px; height: 1px; }
  .divider--light { top: 137px; background: var(--white); }
  .divider--dark { top: 496px; background: var(--rule-grey); }
  .divider__mark { position: absolute; left: 75px; top: -19px; width: 24px; height: 20px; border-radius: 50% 50% 40% 40%; }
  .divider--light .divider__mark { background: var(--white); }
  .divider--dark .divider__mark { background: var(--ink); }

  .subscribe-form { position: absolute; top: 181px; left: 382px; display: flex; gap: 16px; }
  .subscribe-form__input { width: 248px; height: 39px; background: var(--input-bg); border: 1px solid #f5f5f5; font-family: "Roboto", sans-serif; font-size: 18px; color: #333; display: flex; align-items: center; justify-content: center; }
  .subscribe-form__button { width: 150px; height: 39px; background: var(--button-blue); color: var(--white); font-family: "Roboto", sans-serif; font-size: 26px; display: flex; align-items: center; justify-content: center; }

  .events__title { position: absolute; left: 0; width: 100%; top: 416px; text-align: center; font-family: "Courgette", cursive; font-size: 50px; line-height: 64px; color: var(--ink); }

  .event-card { position: absolute; background: var(--card-bg); }
  .event-card__text { position: absolute; left: 25px; width: 400px; text-align: center; }
  .event-card__name { font-family: "Open Sans", sans-serif; font-weight: 700; font-size: 22px; line-height: 30px; color: var(--ink); margin-top: 36px; }
  .event-card__body { margin-top: 23px; font-size: 12.4px; line-height: 22.6px; color: var(--body-text); }

  .event-date { position: absolute; width: 407px; height: 348px; background: var(--plum); }
  .event-date__frame { position: absolute; left: 15px; top: 15px; width: 377px; height: 318px; border: 1px solid var(--frame-line); }
  .event-date__graphic { position: absolute; left: 0; top: 0; }
  .event-date__when { position: absolute; left: 108px; width: 190px; top: 157px; text-align: center; font-family: "Courgette", cursive; font-size: 25px; line-height: 36px; color: var(--white); }
</style>
</head>
<body>

<section class="subscription">
  <div class="subscription__frame"></div>
  <h2 class="subscription__title">Email Subscription</h2>
  <div class="divider divider--light"><div class="divider__mark" role="img" aria-label="Small sitting cat emblem"></div></div>
  <form class="subscribe-form">
    <div class="subscribe-form__input">Your Email Here</div>
    <div class="subscribe-form__button">SUBSCRIBE</div>
  </form>
</section>

<h2 class="events__title">The Animals Events</h2>
<div class="divider divider--dark"><div class="divider__mark" role="img" aria-label="Small sitting cat emblem"></div></div>

<article class="event-card" style="left:156px; top:595px; width:881px; height:302px;">
  <div class="event-card__text">
    <h3 class="event-card__name">First Ceremony</h3>
    <p class="event-card__body">Lorem ipsum dolor sit amet, consectetur adipiscing elit, sed do eiusmod tempor incididunt ut labore et dolore magna aliqua. Ut enim ad minim veniam, quis nostrud exercitation ullamco laboris nisi ut aliquip commodo consequat. Duis aute irure dolor in reprehenderit in voluptate velit esse cillum dolore eu fugiat nulla pariatur. Excepteur sint occaecat cupidatat non proident, sunt in culpa qui officia deserunt mollit anim id est laborum. Lorem ipsum dolor sit amet, consectetur adipiscing elit, sed do eiusmod tempor incididunt ut labore et dolore magna aliqua.</p>
  </div>
</article>

<div class="event-date" style="left:608px; top:573px;">
  <div class="event-date__frame"></div>
  <svg class="event-date__graphic" width="407" height="348" viewBox="0 0 407 348">
    <circle cx="203" cy="174" r="94" fill="none" stroke="#fff" stroke-width="2"/>
    <g fill="#fff">
      <circle cx="7" cy="174" r="2"/><circle cx="19" cy="174" r="2"/><circle cx="31" cy="174" r="2"/>
      <circle cx="43" cy="174" r="2"/><circle cx="55" cy="174" r="2"/><circle cx="67" cy="174" r="2"/>
      <circle cx="79" cy="174" r="2.5"/><circle cx="95" cy="174" r="4"/>
    </g>
    <g fill="none" stroke="#fff" stroke-width="1.5">
      <rect x="195" y="118" width="16" height="15"/>
      <line x1="195" y1="122" x2="211" y2="122"/>
      <line x1="199" y1="116" x2="199" y2="120"/><line x1="207" y1="116" x2="207" y2="120"/>
      <line x1="200" y1="122" x2="200" y2="133"/><line x1="206" y1="122" x2="206" y2="133"/>
      <line x1="195" y1="126" x2="211" y2="126"/><line x1="195" y1="130" x2="211" y2="130"/>
    </g>
  </svg>
  <div class="event-date__when">23 July 2015<br>10:00 AM</div>
</div>

<article class="event-card" style="left:178px; top:996px; width:881px; height:302px;"></article>
<div class="event-date" style="left:178px; top:973px;">
  <div class="event-date__frame"></div>
</div>

</body>
</html>
```